Website for Excavator and Earthworks Company

We require a modern, sleek and practical website for our newly created earthworks/excavator business in Perth, Western Australia called Bluegum Ridge Earthworks.

The website should have a modern, cutting edge feel but only needs to be relatively simplistic in it's layout and eventual functionality.

Some pages it should have would be Home, About, Projects and Contact Us.

```html
<!DOCTYPE html>
<html lang="en">
<head>
<meta charset="utf-8">
<title>Bluegum Ridge Earthworks</title>
<link href="https://fonts.googleapis.com/css2?family=Saira:wght@400;600;700&family=Sora:wght@400;500;600&display=swap" rel="stylesheet">
<style>
:root{
  --lime:#c3dc05;
  --lime-dark:#9fb500;
  --ink:#111111;
  --black:#050505;
  --white:#ffffff;
  --cream:#f6f9dd;
  --grey:#555555;
  --line:#e6e6e6;
}
*{box-sizing:border-box;margin:0;padding:0}
html,body{width:1200px;height:4286px;overflow:hidden}
body{position:relative;background:var(--white);font-family:"Sora",sans-serif;color:var(--ink)}
.abs{position:absolute}
.heading{font-family:"Saira",sans-serif;font-weight:700;text-transform:uppercase;color:var(--ink)}
.eyebrow{font-family:"Saira",sans-serif;font-size:14px;font-weight:600;color:var(--lime);text-transform:uppercase;display:flex;align-items:center;gap:12px}
.eyebrow::before{content:"";width:36px;height:3px;background:var(--lime)}
.btn{display:flex;align-items:center;justify-content:center;gap:10px;background:var(--lime);color:var(--ink);font-size:14px;font-weight:500;height:40px}
.btn svg{width:14px;height:14px}
.photo{overflow:hidden}
.nav a,.foot-nav a{font-family:"Saira",sans-serif;font-size:13px;font-weight:600;letter-spacing:2px;color:var(--white);text-decoration:none;text-transform:uppercase}
.contact{display:flex;gap:16px;align-items:center;color:var(--white)}
.contact .ico{width:36px;height:36px;background:var(--lime);display:flex;align-items:center;justify-content:center}
.contact .ico svg{width:18px;height:18px}
.contact .lbl{font-size:12px;font-weight:500;text-transform:uppercase}
.contact .val{font-size:13px;font-weight:600}
.brand{font-family:"Saira",sans-serif;font-weight:600;color:var(--white);text-transform:uppercase;letter-spacing:2px}
/* hero */
.hero{left:0;top:0;width:1200px;height:700px;background:var(--black);overflow:hidden}
.hero-photo{left:520px;top:0;width:680px;height:700px;background:linear-gradient(90deg,#050505 0%,rgba(5,5,5,0) 30%),linear-gradient(200deg,#5c86c0 0%,#3e5f8a 30%,#c9a022 55%,#6e4a2c 78%,#3b2a1c 100%)}
.hero-title{left:150px;top:222px;font-family:"Saira",sans-serif;text-transform:uppercase;line-height:1.1}
.hero-title .l1{font-size:50px;font-weight:700;color:var(--lime)}
.hero-title .l2{font-size:46px;font-weight:400;color:var(--lime);letter-spacing:1px}
/* services */
.card-cap{font-family:"Saira",sans-serif;font-weight:600;font-size:14px;text-transform:uppercase;line-height:1.8}
/* why */
.why-label{font-family:"Saira",sans-serif;font-weight:600;font-size:15px;text-transform:uppercase;white-space:nowrap}
.why-icon{width:64px;height:64px;border-radius:50%;background:var(--lime);display:flex;align-items:center;justify-content:center}
.why-icon svg{width:34px;height:34px}
.para{font-size:13px;line-height:22px;color:var(--grey);text-align:justify}
</style>
</head>
<body>

<!-- HERO -->
<header class="abs hero">
  <div class="abs hero-photo" role="img" aria-label="Yellow excavator digging soil under a blue sky"></div>
  <div class="abs brand" style="left:150px;top:30px;width:220px;font-size:22px;line-height:1.15">Bluegum Ridge<br>Earthworks</div>
  <div class="abs contact" style="left:582px;top:22px">
    <div class="ico"><svg viewBox="0 0 24 24" fill="none" stroke="#111" stroke-width="2"><rect x="3" y="5" width="18" height="14"/><path d="M3 6l9 7 9-7"/></svg></div>
    <div><div class="lbl">Email</div><div class="val">info@bluegumridgeworks.com.au</div></div>
  </div>
  <div class="abs contact" style="left:879px;top:22px">
    <div class="ico"><svg viewBox="0 0 24 24" fill="#111"><path d="M6.6 10.8a15 15 0 006.6 6.6l2.2-2.2a1 1 0 011-.25 11.4 11.4 0 003.6.57 1 1 0 011 1V20a1 1 0 01-1 1A17 17 0 013 4a1 1 0 011-1h3.5a1 1 0 011 1c0 1.25.2 2.45.57 3.6a1 1 0 01-.25 1z"/></svg></div>
    <div><div class="lbl">Call Us</div><div class="val">+61 8 5550 0142</div></div>
  </div>
  <nav class="abs nav" style="left:607px;top:92px;display:flex;gap:0">
    <a style="position:absolute;left:0;color:var(--lime)">Home</a>
    <a style="position:absolute;left:102px">About</a>
    <a style="position:absolute;left:208px">Projects</a>
    <a style="position:absolute;left:345px;white-space:nowrap">Contact Us</a>
  </nav>
  <h1 class="abs hero-title"><div class="l1">Bluegum Ridge</div><div class="l2">Earthworks</div></h1>
  <div class="abs" style="left:150px;top:345px;font-family:'Saira',sans-serif;font-weight:700;font-size:15px;color:var(--white);text-transform:uppercase">Precision Earthmoving Excavation in Perth</div>
  <p class="abs" style="left:150px;top:380px;width:360px;font-size:12.5px;line-height:24px;color:#d8d8d8">Reliable, efficient, and modern earthworks solutions for residential, commercial, and civil projects.</p>
  <div class="abs btn" style="left:150px;top:444px;width:140px">Get a Quote <svg viewBox="0 0 16 16"><circle cx="8" cy="8" r="8" fill="#111"/><path d="M7 5l3 3-3 3" stroke="#c3dc05" stroke-width="2" fill="none"/></svg></div>
  <svg class="abs" style="left:0;top:580px" width="1200" height="120" viewBox="0 0 1200 120">
    <polygon points="0,85 600,8 1200,92 1200,120 0,120" fill="#c3dc05"/>
    <polygon points="0,120 600,20 1200,120" fill="#ffffff"/>
  </svg>
</header>

<!-- ABOUT -->
<section class="abs" style="left:0;top:700px;width:1200px;height:660px">
  <div class="abs" style="left:850px;top:420px;width:350px;height:240px;background:linear-gradient(160deg,rgba(255,255,255,0) 30%,#f1f1f1 100%)" role="img" aria-label="Faint line drawing of terraced hillside earthworks"></div>
  <div class="abs photo" style="left:150px;top:69px;width:442px;height:449px;background:linear-gradient(180deg,#6aa0d8 0%,#b9d1ea 35%,#d3a22a 55%,#6d4a2d 80%,#4a3424 100%)" role="img" aria-label="Backhoe loader moving dirt on a building site"></div>
  <div class="abs eyebrow" style="left:644px;top:87px">About</div>
  <h2 class="abs heading" style="left:644px;top:112px;font-size:36px;line-height:45px">Built on Precision<br>Reliability</h2>
  <p class="abs para" style="left:644px;top:216px;width:406px">Bluegum Ridge Earthworks is a Perth-based earthmoving and excavation company delivering efficient, high-quality groundwork solutions. We combine modern machinery, skilled operators, and a commitment to safety and accuracy on every job.</p>
  <p class="abs para" style="left:644px;top:346px;width:406px">Whether it's residential site preparation, commercial earthworks, or civil support work, we approach every project with professionalism, attention to detail, and respect for timelines.</p>
  <div class="abs btn" style="left:644px;top:452px;width:140px">Read More <svg viewBox="0 0 16 16"><circle cx="8" cy="8" r="8" fill="#111"/><path d="M7 5l3 3-3 3" stroke="#c3dc05" stroke-width="2" fill="none"/></svg></div>
</section>

<!-- SERVICES -->
<section class="abs" style="left:0;top:1360px;width:1200px;height:738px;background:var(--cream)">
  <div class="abs eyebrow" style="left:151px;top:83px">Our Services</div>
  <h2 class="abs heading" style="left:151px;top:112px;font-size:36px;line-height:45px">Complete Earthworks<br>Services</h2>
  <div class="abs" style="left:953px;top:110px;width:44px;height:40px;background:var(--lime);display:flex;align-items:center;justify-content:center"><svg width="20" height="20" viewBox="0 0 16 16"><circle cx="8" cy="8" r="8" fill="#111"/><path d="M9 5l-3 3 3 3" stroke="#c3dc05" stroke-width="2" fill="none"/></svg></div>
  <div class="abs" style="left:1005px;top:110px;width:44px;height:40px;background:var(--lime);display:flex;align-items:center;justify-content:center"><svg width="20" height="20" viewBox="0 0 16 16"><circle cx="8" cy="8" r="8" fill="#111"/><path d="M7 5l3 3-3 3" stroke="#c3dc05" stroke-width="2" fill="none"/></svg></div>

  <div class="abs photo" style="left:151px;top:241px;width:252px;height:270px;background:linear-gradient(170deg,#8d8b86 0%,#d99a45 45%,#7a5a36 75%,#2f2a24 100%)" role="img" aria-label="Wheel loader filling a dump truck at sunset"></div>
  <div class="abs card-cap" style="left:159px;top:521px">Earthmoving &amp; Excavation</div>

  <div class="abs photo" style="left:424px;top:241px;width:250px;height:355px;background:linear-gradient(180deg,#3f6d34 0%,#567d3e 40%,#8f8f8c 65%,#c9a52c 85%,#6a5a3b 100%)" role="img" aria-label="Grader levelling a gravel road through forest"></div>
  <div class="abs card-cap" style="left:431px;top:610px">Site Preparation &amp;<br>Clearing</div>

  <div class="abs photo" style="left:684px;top:241px;width:251px;height:270px;background:linear-gradient(180deg,#e8a34a 0%,#c97b36 40%,#5b3d29 75%,#2c2019 100%)" role="img" aria-label="Excavator beside large drainage pipes in a trench"></div>
  <div class="abs card-cap" style="left:701px;top:521px">Trenching &amp; Drainage</div>

  <div class="abs photo" style="left:957px;top:241px;width:243px;height:355px;background:linear-gradient(160deg,#d9a52a 0%,#c5382e 25%,#6d7072 55%,#3a3b3c 100%)" role="img" aria-label="Concrete truck pouring a foundation slab"></div>
  <div class="abs card-cap" style="left:971px;top:610px">Foundations &amp; Pad Prep</div>
</section>

<!-- WHY -->
<section class="abs" style="left:0;top:2098px;width:1200px;height:694px">
  <div class="abs eyebrow" style="left:0;width:1200px;top:102px;justify-content:center">Value Proposition</div>
  <h2 class="abs heading" style="left:0;width:1200px;top:130px;text-align:center;font-size:34px;font-weight:600">Why Bluegum Ridge Earthworks</h2>
  <svg class="abs" style="left:429px;top:216px" width="340" height="340" viewBox="0 0 340 340">
    <circle cx="170" cy="170" r="166" fill="none" stroke="#f0f0f0" stroke-width="4"/>
    <circle cx="170" cy="170" r="124" fill="#ffffff" stroke="#ececec" stroke-width="3"/>
  </svg>
  <div class="abs brand" style="left:499px;top:356px;width:200px;text-align:center;color:var(--lime);font-size:24px;line-height:1.1">Bluegum<br>Ridge</div>

  <div class="abs why-icon" style="left:454px;top:233px"><svg viewBox="0 0 24 24" fill="none" stroke="#111" stroke-width="1.5"><rect x="3" y="7" width="18" height="11" rx="2"/><path d="M7 7V5h10v2M7 11h2v3H7zM11 11h2v3h-2zM15 11h2v3h-2z"/></svg></div>
  <div class="abs why-icon" style="left:684px;top:233px"><svg viewBox="0 0 24 24" fill="none" stroke="#111" stroke-width="1.5"><path d="M12 3l7 3v5c0 5-3 8-7 10-4-2-7-5-7-10V6z"/><path d="M12 8v6M9 11h6"/></svg></div>
  <div class="abs why-icon" style="left:404px;top:354px"><svg viewBox="0 0 24 24" fill="none" stroke="#111" stroke-width="1.5"><rect x="3" y="5" width="15" height="15" rx="1"/><path d="M3 9h15M7 3v4M14 3v4"/><circle cx="18" cy="17" r="4" fill="#c3dc05"/><path d="M18 15v2l1.5 1"/></svg></div>
  <div class="abs why-icon" style="left:735px;top:354px"><svg viewBox="0 0 24 24" fill="none" stroke="#111" stroke-width="1.5"><circle cx="12" cy="9" r="5"/><path d="M9 13l-2 8 5-3 5 3-2-8"/></svg></div>
  <div class="abs why-icon" style="left:454px;top:479px"><svg viewBox="0 0 24 24" fill="none" stroke="#111" stroke-width="1.5"><circle cx="9" cy="6" r="3"/><path d="M4 20v-5a5 5 0 0110 0v5M15 9l5 5-2 2-5-5"/></svg></div>
  <div class="abs why-icon" style="left:684px;top:479px"><svg viewBox="0 0 24 24" fill="none" stroke="#111" stroke-width="1.5"><path d="M12 21s-6-6-6-11a6 6 0 0112 0c0 5-6 11-6 11z"/><circle cx="12" cy="10" r="2"/></svg></div>

  <div class="abs why-label" style="right:796px;top:256px">Modern Equipment</div>
  <div class="abs why-label" style="right:829px;top:377px">Reliable Scheduling</div>
  <div class="abs why-label" style="right:796px;top:502px">Skilled Operators</div>
  <div class="abs why-label" style="left:784px;top:256px">Safety-First Approach</div>
  <div class="abs why-label" style="left:829px;top:377px">Quality Workmanship</div>
  <div class="abs why-label" style="left:784px;top:502px">Perth-Based &amp; Locally Owned</div>
</section>

<!-- PROJECTS -->
<section class="abs" style="left:0;top:2792px;width:1200px;height:1000px;background:linear-gradient(135deg,#eef2cc 0%,#f4f6dc 45%,#e9edc4 100%)" role="img" aria-label="Faded aerial view of an earthworks site behind the gallery">
  <div class="abs eyebrow" style="left:151px;top:98px">Projects</div>
  <h2 class="abs heading" style="left:151px;top:128px;font-size:36px;line-height:45px">Our Equipment<br>Fleet</h2>
  <div class="abs btn" style="left:150px;top:240px;width:170px">Explore Gallery <svg viewBox="0 0 16 16"><circle cx="8" cy="8" r="8" fill="#111"/><path d="M7 5l3 3-3 3" stroke="#c3dc05" stroke-width="2" fill="none"/></svg></div>

  <div class="abs photo" style="left:720px;top:93px;width:458px;height:375px;background:linear-gradient(180deg,#b7cf3c 0%,#98b52a 45%,#7f9a22 75%,#a5bd2b 100%)" role="img" aria-label="Excavator clearing timber in a pine forest, lime tinted"></div>
  <svg class="abs" style="left:936px;top:269px" width="24" height="24" viewBox="0 0 24 24"><circle cx="12" cy="12" r="11" fill="#ffffff"/><path d="M12 7v10M7 12h10" stroke="#9fb500" stroke-width="2.5"/></svg>

  <div class="abs photo" style="left:403px;top:296px;width:296px;height:165px;background:linear-gradient(170deg,#8c8a85 0%,#d99a45 45%,#6a4e31 80%,#2c2620 100%)" role="img" aria-label="Wheel loader and dump truck at sunset"></div>
  <div class="abs photo" style="left:401px;top:481px;width:218px;height:250px;background:linear-gradient(180deg,#cf9a4a 0%,#8a5a33 40%,#3a79c8 75%,#6a4a30 100%)" role="img" aria-label="Blue water pipes laid in an open trench"></div>
  <div class="abs photo" style="left:641px;top:484px;width:297px;height:346px;background:linear-gradient(180deg,#5d8fd0 0%,#a9c6e8 30%,#d58f2c 55%,#2d2f33 80%,#6a5040 100%)" role="img" aria-label="Excavator lifting a large black pipe"></div>
  <div class="abs photo" style="left:962px;top:481px;width:216px;height:171px;background:linear-gradient(180deg,#d7a66c 0%,#8a5d3a 40%,#3b3d42 75%,#5a4434 100%)" role="img" aria-label="Pipeline sections in a long trench"></div>
</section>

<!-- FOOTER -->
<footer class="abs" style="left:0;top:3740px;width:1200px;height:546px">
  <svg class="abs" style="left:0;top:0" width="1200" height="546" viewBox="0 0 1200 546">
    <polygon points="0,82 600,10 1200,72 1200,110 0,110" fill="#c3dc05"/>
    <polygon points="0,112 600,16 1200,104 1200,546 0,546" fill="#050505"/>
  </svg>
  <div class="abs brand" style="left:0;width:1200px;top:130px;text-align:center;font-size:36px;line-height:1.15">Bluegum Ridge<br>Earthworks</div>
  <div class="abs contact" style="left:366px;top:305px">
    <div class="ico"><svg viewBox="0 0 24 24" fill="none" stroke="#111" stroke-width="2"><rect x="3" y="5" width="18" height="14"/><path d="M3 6l9 7 9-7"/></svg></div>
    <div><div class="lbl">Email</div><div class="val">info@bluegumridgeworks.com.au</div></div>
  </div>
  <div class="abs contact" style="left:662px;top:305px">
    <div class="ico"><svg viewBox="0 0 24 24" fill="#111"><path d="M6.6 10.8a15 15 0 006.6 6.6l2.2-2.2a1 1 0 011-.25 11.4 11.4 0 003.6.57 1 1 0 011 1V20a1 1 0 01-1 1A17 17 0 013 4a1 1 0 011-1h3.5a1 1 0 011 1c0 1.25.2 2.45.57 3.6a1 1 0 01-.25 1z"/></svg></div>
    <div><div class="lbl">Call Us</div><div class="val">+61 8 5550 0142</div></div>
  </div>
  <nav class="abs foot-nav" style="left:0;top:390px;width:1200px;height:20px">
    <a class="abs" style="left:380px">Home</a>
    <a class="abs" style="left:479px">About</a>
    <a class="abs" style="left:587px">Projects</a>
    <a class="abs" style="left:722px;white-space:nowrap">Contact Us</a>
  </nav>
  <div class="abs" style="left:150px;top:456px;width:900px;height:1px;background:#333"></div>
  <div class="abs" style="left:0;width:1200px;top:487px;text-align:center;font-size:13px;color:var(--white)">copyright 2026.Company Name. all rights reserved</div>
</footer>

</body>
</html>
```